San Francisco Leading Consulting firm - 47Vora Web Design Project

•Create a Web Design
•Uncoded webpage layout design
•2 Pages Design - Homepage + Interior Page

Task Description
Hello, we're looking for a re-design our current website www.47vora-example.com

we have a sample mockup design @

http://47vora.pubtrellis-example.org/

This shows the layout that we like and also a sample of 6 pictures that would change based on where you mouse over..

6 pictures HOME design needs to be included.

SMART
THOUGHTFUL
FLEXIBLE
CREATIVE SERVICES
TECHNICAL SERVICES
PARTNERS

sites we like:

http://www.melvanadvisory-example.com/Home.cfm?id=Home
http://www.plinthworks-example.com/index.html

Our company can be best described as: 100+ employees, cutting-edge, depandable, innovative, strong, smart.

Our Primary focus is: IT Consulting Services and Creative Design services

47Vora LLC is a consulting firm providing creative design, business and technology solutions to both private and public interests.

Established in 1996, 47Vora is a San Francisco based company providing specialists for a range of business needs including:

Creative Design Services
•Print
•Logo Design
•Website Design
•Illustration

and

Business and Technology solutions

•Application Software and Web Development
•Business Process Re-Design (BPR)
•Business/Systems Analysis and Requirement Documentation
•Mentoring and Training
•Network/Hardware Installation Services
•System Design and Architecture
•Vendor Management
•Ledgerfold Architecture and Implementation

our sample mockup site:

Reason: Due to holiday season, we're not available to work with designers and finilize our design.  

Thank you very much for submitting your design.

We appreciate your time and creativity.   Since, our office is currently closed for holidays, we will be reviewing it in details next week and will make our decision as soon as possible.

It would be great if you could submit any of your changes by Wed next week, so it would be part of our reviews. 

Please see updated wireframe under attachments:  we have some minor updates to our wireframe that we would like you to update your designs, if possible.  

We also encorouge you not to use our standard wireframe and come up with more unique designs.   Everything would be considered when we review your design.

 

Target Market(s)

Creative services and professional services clients, including government agencies

Industry/Entity Type

Business

Requirements
Must have
• Clean, professional look, easy navigation

```html
<!DOCTYPE html>
<html lang="en">
<head>
<meta charset="utf-8">
<title>47Vora — Technology Solutions</title>
<link rel="stylesheet" href="https://fonts.googleapis.com/css2?family=Arimo:wght@400;700&family=Open+Sans:wght@300;400&display=swap">
<style>
:root{
  --sky-top:#e9f8fc;
  --sky-bottom:#c2eef9;
  --panel:#ffffff;
  --cyan:#27c4ec;
  --cyan-dark:#19a9d8;
  --ink:#1e1e1e;
  --nav-ink:#3a3a3a;
  --orange:#f5a623;
  --band:#8c8c8c;
  --brand-ink:#2b6f9e;
}
*{box-sizing:border-box;margin:0;padding:0}
html,body{width:1200px;height:1196px;overflow:hidden}
body{
  position:relative;
  font-family:"Arimo",Arial,sans-serif;
  color:var(--ink);
  background:linear-gradient(180deg,var(--sky-top) 0%,#d9f4fb 45%,var(--sky-bottom) 100%);
}
.brand{position:absolute;left:183px;top:30px;display:flex;align-items:center;gap:8px}
.brand-mark{width:22px;height:22px;border-radius:50%;background:var(--cyan-dark)}
.brand-name{font-size:24px;font-weight:400;color:var(--brand-ink);letter-spacing:1px}
.tagline{position:absolute;left:356px;top:60px;font-size:11px;color:#444;border-left:1px solid #888;padding-left:7px;line-height:15px}

.main-nav{position:absolute;left:154px;top:98px;width:883px;height:43px;background:#fff;border-radius:6px;box-shadow:0 1px 4px rgba(0,0,0,.15)}
.nav-home{position:absolute;left:0;top:0;width:41px;height:43px;border-radius:6px 0 0 6px;background:linear-gradient(180deg,#6fd6f3,#25b5e2);display:flex;align-items:center;justify-content:center}
.nav-item{position:absolute;top:15px;font-size:10.5px;font-weight:700;letter-spacing:.6px;color:var(--nav-ink)}
.nav-item .chev{color:var(--orange);margin-left:4px}
.search{position:absolute;left:728px;top:12px;width:145px;height:20px;border:1px solid #cfd8dc;border-radius:2px;font-size:7px;color:#9aa;padding:5px 7px;letter-spacing:.5px}
.search svg{position:absolute;right:4px;top:3px}

.content{position:absolute;left:154px;top:157px;width:883px;height:991px;background:var(--panel);border-radius:8px;box-shadow:0 1px 6px rgba(0,0,0,.12)}
.welcome{position:absolute;left:15px;top:4px;font-family:"Open Sans",Arial,sans-serif;font-size:33px;font-weight:400;color:var(--cyan)}
.intro{position:absolute;left:19px;font-size:10.4px;color:var(--ink);white-space:nowrap}
.intro-1{top:52px}.intro-2{top:80px}

.slider-thumbs{position:absolute;left:39px;top:125px;width:110px;height:393px;background:#fff;box-shadow:0 0 5px rgba(0,0,0,.25)}
.thumb{position:absolute;left:8px;width:94px;height:53px}
.thumb-marker{position:absolute;left:102px;width:6px;height:53px;background:var(--orange)}
.slider-stage{position:absolute;left:156px;top:125px;width:687px;height:393px;background:#fff;box-shadow:0 0 5px rgba(0,0,0,.25)}
.stage-photo{position:absolute;left:9px;top:9px;width:669px;height:375px;background:linear-gradient(180deg,#eef1f3 0%,#d9dfe3 40%,#8d8f8f 75%,#4f5050 100%)}
.stage-caption{position:absolute;left:19px;top:274px;width:660px;height:46px;background:rgba(255,255,255,.75);font-family:"Open Sans",Arial,sans-serif;font-size:30px;font-weight:300;color:#111;padding-left:12px;line-height:46px}
.caption-icon{position:absolute;right:14px;top:-8px;width:52px;height:56px;border-radius:50%;background:linear-gradient(135deg,#e7ecef,#aab5bb)}
.arrow{position:absolute;top:182px;width:20px;height:34px;background:rgba(0,0,0,.35);display:flex;align-items:center;justify-content:center}
.arrow-prev{left:9px}.arrow-next{right:9px}

.card{position:absolute;top:545px;width:279px;height:258px;background:#fff;box-shadow:0 0 5px rgba(0,0,0,.25)}
.card-head{position:absolute;left:-4px;top:4px;width:283px;height:28px;background:var(--band);color:#fff;font-size:13.5px;padding-left:32px;line-height:28px}
.card-head .tab{position:absolute;left:0;top:0;width:24px;height:28px;background:var(--cyan);display:flex;align-items:center;justify-content:center}
.card-media{position:absolute;left:12px;top:46px;width:256px;height:80px}
.media-text{position:absolute;font-size:12px;font-weight:700;line-height:15px;letter-spacing:.5px}
.card-text{position:absolute;left:13px;top:140px;width:256px;font-size:10.6px;line-height:20px;color:#333}
.btn-more{position:absolute;right:12px;top:220px;width:74px;height:28px;background:linear-gradient(180deg,#7ddbf5,#2cb8e6);border-radius:3px;color:#fff;font-size:11px;line-height:28px;text-align:center}

.services-title{position:absolute;top:835px;font-size:12.5px;font-weight:700;color:#3b3b3b;letter-spacing:.3px}
.service-list{position:absolute;top:866px;list-style:none;font-size:9.5px;color:#333}
.service-list li{height:24.5px;padding-left:8px;position:relative;line-height:12px}
.service-list li::before{content:"";position:absolute;left:0;top:4px;width:3px;height:3px;border-radius:50%;background:#333}
.service-list li.two{height:37px}
.copyright{position:absolute;top:1161px;width:1200px;text-align:center;font-size:10px;color:#222}
</style>
</head>
<body>

<header>
  <div class="brand"><span class="brand-mark"></span><span class="brand-name">47Vora</span></div>
  <div class="tagline">Thechnology Solutions for the 21st Century</div>
</header>

<nav class="main-nav">
  <div class="nav-home">
    <svg width="14" height="13" viewBox="0 0 14 13"><path d="M7 0 0 6h2v7h4V9h2v4h4V6h2z" fill="#fff"/></svg>
  </div>
  <span class="nav-item" style="left:56px">COMPANY<span class="chev">›</span></span>
  <span class="nav-item" style="left:156px">TECHNICAL SERVICES<span class="chev">›</span></span>
  <span class="nav-item" style="left:320px">CREATIVE SERVICES<span class="chev">›</span></span>
  <span class="nav-item" style="left:480px">PARTNERS<span class="chev">›</span></span>
  <span class="nav-item" style="left:588px">CONTACT US</span>
  <div class="search">SEARCH
    <svg width="12" height="12" viewBox="0 0 12 12"><circle cx="7" cy="5" r="3.5" fill="none" stroke="#f5a623" stroke-width="1.5"/><path d="M4.5 7.5 1 11" stroke="#f5a623" stroke-width="1.8"/></svg>
  </div>
</nav>

<main class="content">
  <h1 class="welcome">welcome</h1>
  <p class="intro intro-1">47Vora LLC is a consulting firm providing creative design, business and technology solutions to both private and public interests.</p>
  <p class="intro intro-2">Our experts possess broad industry knowledge which can help with technical and businessprocess challenges, delivering solutions that are creative and cost effective.</p>

  <div class="slider-thumbs">
    <div class="thumb" style="top:13px;background:linear-gradient(135deg,#f2f2f2,#9a9a9a)" role="img" aria-label="Thumbnail: figures assembling puzzle pieces"></div>
    <div class="thumb" style="top:77px;background:linear-gradient(135deg,#6b5a4c,#c9c2b8)" role="img" aria-label="Thumbnail: person working at a laptop"></div>
    <div class="thumb" style="top:140px;background:linear-gradient(180deg,#3f9fd0,#6ab84a)" role="img" aria-label="Thumbnail: person leaping over green hills"></div>
    <div class="thumb" style="top:202px;background:linear-gradient(135deg,#1d2a2a,#c85a3a 60%,#3a8a3c)" role="img" aria-label="Thumbnail: colored pencils"></div>
    <div class="thumb" style="top:264px;background:linear-gradient(180deg,#e7e9eb,#4a4a4a)" role="img" aria-label="Thumbnail: business people walking"></div>
    <div class="thumb-marker" style="top:264px"></div>
    <div class="thumb" style="top:326px;background:linear-gradient(135deg,#0d3d7a,#7ac4ee)" role="img" aria-label="Thumbnail: handshake before glass building"></div>
  </div>

  <div class="slider-stage">
    <div class="stage-photo" role="img" aria-label="Business people meeting on a bridge with commuters passing"></div>
    <div class="arrow arrow-prev"><svg width="8" height="12" viewBox="0 0 8 12"><path d="M7 1 2 6l5 5" stroke="#fff" stroke-width="2" fill="none"/></svg></div>
    <div class="arrow arrow-next"><svg width="8" height="12" viewBox="0 0 8 12"><path d="M1 1l5 5-5 5" stroke="#fff" stroke-width="2" fill="none"/></svg></div>
    <div class="stage-caption">technical services
      <div class="caption-icon" role="img" aria-label="Head outline with colored gears"></div>
    </div>
  </div>

  <section class="card" style="left:8px">
    <div class="card-head"><span class="tab"><svg width="7" height="10" viewBox="0 0 7 10"><path d="M1 1l4 4-4 4" stroke="#fff" stroke-width="2" fill="none"/></svg></span>for graphic designers</div>
    <div class="card-media" role="img" aria-label="Purple creative head illustration with pink swoosh" style="background:linear-gradient(90deg,#7a2a8a 0%,#fff 40%,#fde3ec 100%)">
      <span class="media-text" style="left:60px;top:14px;color:#b0123a">GET<br>CREATIVE !</span>
    </div>
    <p class="card-text">47Vora is looking for top creative talent to deliver graphic design solutions for some leading global brands Do you have what it takes?</p>
    <span class="btn-more">Learn More</span>
  </section>

  <section class="card" style="left:301px">
    <div class="card-head"><span class="tab"><svg width="7" height="10" viewBox="0 0 7 10"><path d="M1 1l4 4-4 4" stroke="#fff" stroke-width="2" fill="none"/></svg></span>for clients</div>
    <div class="card-media" role="img" aria-label="Red figure running across gray crowd" style="background:linear-gradient(90deg,#cfcfcf,#9d9d9d)">
      <span class="media-text" style="right:10px;top:46px;color:#fff;text-align:right">THE 47VORA<br>DIFFERENCE</span>
    </div>
    <p class="card-text">Smart, Flexible, Thoughtful: find out why leading corporations and government agencies are turning to 47vora to help manage their most demanding IT services challenges.</p>
    <span class="btn-more">Learn More</span>
  </section>

  <section class="card" style="left:593px">
    <div class="card-head"><span class="tab"><svg width="7" height="10" viewBox="0 0 7 10"><path d="M1 1l4 4-4 4" stroke="#fff" stroke-width="2" fill="none"/></svg></span>for partners</div>
    <div class="card-media" role="img" aria-label="Handshake in front of city towers" style="background:linear-gradient(90deg,#2a2a2a,#8a8f93 50%,#3c4046)">
      <span class="media-text" style="left:6px;top:46px;color:#fff">TEAM UP<br>WITH THE BEST</span>
    </div>
    <p class="card-text">When it comes to technology partnerships,<br>our mission it so make you a success.</p>
    <span class="btn-more">Learn More</span>
  </section>

  <h2 class="services-title" style="left:43px">Creative Design Services</h2>
  <ul class="service-list" style="left:56px">
    <li>Print</li><li>Logo Design</li><li>Website Design</li><li>Illustration</li>
  </ul>

  <h2 class="services-title" style="left:348px">Business and Technology solutions</h2>
  <ul class="service-list" style="left:362px;width:215px">
    <li>Application Software and Web Development</li>
    <li>Business Process Re-Design (BPR)</li>
    <li class="two">Business/Systems Analysis and Requirement Documentation</li>
    <li>Mentoring and Training</li>
  </ul>
  <ul class="service-list" style="left:613px">
    <li>Network/Hardware Installation Services</li>
    <li>System Design and Architecture</li>
    <li>Vendor Management</li>
    <li>Ledgerfold Architecture and Implementation</li>
  </ul>
</main>

<footer class="copyright">Copyright 2010, 47Vora, LLC All rights reserved.</footer>

</body>
</html>
```